LHP Regal Business Card Design 2020

Your Manor Steward is looking for a business card that is clean and straight to the point but still looks high-end and attractive. We are a team comprised of management and field professionals focused on the high-end residential marketplace. We serve homeowners and trade professionals directly based out of the Metrowest/Boston area. We provide client services as well as construction/renovation services.
We are aiming for a black and white feel (white background and black text) and a matte finish with rounded edges.

We want to emphasis our vision of "Properties - Projects - Partners".
Dana Pellham is the president of LHP

Please include the following areas we service: Boston/Cape/Newport
Please make sure to include Dana's mobile (555) 213 4480 & office number (555) 640 1937, email dana@yourmanorsteward.example and website www.yourmanorsteward.example

Colors

Designer to choose only greyscale colors for use in the design.

Requirements
Must have
• Include "Properties - Projects - Partners" in design

Include "After Hours Emergency Support # 1800 555 0142" with icon

```html
<!DOCTYPE html>
<html lang="en">
<head>
<meta charset="utf-8">
<title>LHP Business Card</title>
<link rel="stylesheet" href="https://fonts.googleapis.com/css2?family=Montserrat:wght@600;700&family=Roboto:wght@400;500&display=swap">
<style>
  :root {
    --backdrop: #8d8d8d;
    --card-black: #151515;
    --card-white: #ffffff;
    --ink: #1a1a1a;
    --silver: #8a8a8a;
    --text-light: #f2f2f2;
    --text-muted: #bdbdbd;
  }
  * { margin: 0; padding: 0; box-sizing: border-box; }
  html, body { width: 1200px; height: 1036px; overflow: hidden; }
  body {
    background: var(--backdrop);
    position: relative;
    font-family: "Roboto", Arial, sans-serif;
  }
  .card {
    position: absolute;
    width: 620px;
    height: 354px;
    border-radius: 10px;
    overflow: hidden;
    box-shadow: 0 10px 28px rgba(0,0,0,0.35);
  }
  .card-front {
    left: 110px; top: 110px;
    background: var(--card-black);
    display: flex; flex-direction: column; align-items: center;
  }
  .wordmark {
    display: flex; flex-direction: column; align-items: center;
    font-family: "Montserrat", Arial, sans-serif;
    font-weight: 700;
  }
  .wordmark-initials { font-size: 96px; line-height: 1; letter-spacing: 2px; }
  .wordmark-name { font-size: 17px; letter-spacing: 4px; margin-top: 10px; }
  .card-front .wordmark { margin-top: 58px; color: var(--silver); }
  .service-areas {
    margin-top: 50px;
    color: var(--text-light);
    font-size: 17px;
    letter-spacing: 0.5px;
  }
  .service-areas .dot {
    display: inline-block; width: 8px; height: 8px; border-radius: 50%;
    background: var(--text-light); margin: 0 7px 2px; vertical-align: middle;
  }
  .vision {
    margin-top: 18px;
    font-family: "Montserrat", Arial, sans-serif;
    font-weight: 600;
    font-size: 12px;
    letter-spacing: 3px;
    color: var(--text-muted);
    text-transform: uppercase;
  }
  .card-back {
    left: 470px; top: 572px;
    display: flex;
  }
  .back-brand {
    width: 52%;
    background: var(--card-white);
    display: flex; align-items: center; justify-content: center;
  }
  .back-brand .wordmark { color: var(--ink); }
  .back-brand .wordmark-initials { font-size: 76px; }
  .back-brand .wordmark-name { font-size: 13px; letter-spacing: 3px; }
  .back-contact {
    width: 48%;
    background: var(--card-black);
    color: var(--text-light);
    padding: 58px 0 0 26px;
  }
  .person-name {
    font-family: "Montserrat", Arial, sans-serif;
    font-weight: 700; font-size: 19px; letter-spacing: 0.5px;
  }
  .person-title {
    font-family: "Montserrat", Arial, sans-serif;
    font-weight: 600; font-size: 14px; margin: 4px 0 18px 10px;
  }
  .contact-list { list-style: none; font-size: 14.5px; }
  .contact-list li { display: flex; align-items: center; gap: 8px; margin-bottom: 5px; white-space: nowrap; }
  .contact-list svg, .emergency svg { width: 14px; height: 14px; flex: none; fill: var(--text-light); }
  .emergency {
    display: flex; align-items: flex-start; gap: 8px;
    margin-top: 16px; padding-top: 12px; margin-right: 26px;
    border-top: 1px solid #3a3a3a;
    font-size: 13px; line-height: 1.35;
  }
  .emergency svg { margin-top: 2px; }
  .emergency-number { font-weight: 500; }
</style>
</head>
<body>
  <section class="card card-front" aria-label="Card front">
    <div class="wordmark">
      <span class="wordmark-initials">LHP</span>
      <span class="wordmark-name">YOUR MANOR STEWARD</span>
    </div>
    <p class="service-areas">
      <span class="dot"></span>Boston <span class="dot"></span>Metrowest <span class="dot"></span>South Shore <span class="dot"></span>Cape <span class="dot"></span>Newport
    </p>
    <p class="vision">Properties - Projects - Partners</p>
  </section>

  <section class="card card-back" aria-label="Card back">
    <div class="back-brand">
      <div class="wordmark">
        <span class="wordmark-initials">LHP</span>
        <span class="wordmark-name">YOUR MANOR STEWARD</span>
      </div>
    </div>
    <div class="back-contact">
      <p class="person-name">DANA PELLHAM</p>
      <p class="person-title">President</p>
      <ul class="contact-list">
        <li><svg viewBox="0 0 14 14"><path d="M4 0h6a1 1 0 0 1 1 1v12a1 1 0 0 1-1 1H4a1 1 0 0 1-1-1V1a1 1 0 0 1 1-1zm.5 1.5v10h5v-10z"/></svg>(555) 213 4480</li>
        <li><svg viewBox="0 0 14 14"><path d="M1 4c0-2 2-3 6-3s6 1 6 3v1H10V3.5H4V5H1zM3 6h8l2 7H1z"/></svg>(555) 640 1937</li>
        <li><svg viewBox="0 0 14 14"><path d="M0 2h14v10H0zm1.5 1.3V11h11V3.3L7 7.5z M2 3l5 3.6L12 3z"/></svg>dana@yourmanorsteward.example</li>
        <li><svg viewBox="0 0 14 14"><path d="M7 0a7 7 0 1 1 0 14A7 7 0 0 1 7 0zm0 1.5a5.5 5.5 0 1 0 0 11 5.5 5.5 0 0 0 0-11z"/><circle cx="7" cy="7" r="3.5"/></svg>www.yourmanorsteward.example</li>
      </ul>
      <div class="emergency">
        <svg viewBox="0 0 14 14"><path d="M7 0.5L13.8 13H0.2zM6.2 5v4.2h1.6V5zm0 5.3v1.6h1.6v-1.6z" fill-rule="evenodd"/></svg>
        <p>After Hours Emergency Support<br><span class="emergency-number"># 1800 555 0142</span></p>
      </div>
    </div>
  </section>
</body>
</html>
```